I have a logo and need to design the business card and stationery.
Updates

The uploaded logo image named as GREYMARSH CONSTRUCTION which is to be replaced to GREYMARSH CONTRACTS. Kindly add below details and submit the designs- Company name- Greymarsh Engineering Contracts LLP Name & Post- Kelvan Joshi (Designated Partner) Address- Block No.317, Wing C, Tulvo Trade Court, Manek Pural Road, Ruparel Industrial Estate, Goregaon(E), Mumbai - 400 063 Contact- +91 97415 60382 Email- kelvanjoshi@mailbrook.example Website- www.greymarshcontracts.example Contact for Letterhead- +91-22-28754193

Hi Tovin Rahul, We are liking your Design #28860835. We have suggested some changes which are mentioned in feedback. Kindly revert with it asap to finalize this design.

Colors

Designer to choose colors to be used in the design.

```html
<!DOCTYPE html>
<html lang="en">
<head>
<meta charset="utf-8">
<title>Greymarsh Contracts – Stationery Set</title>
<link rel="stylesheet" href="https://fonts.googleapis.com/css2?family=Michroma&family=Roboto:wght@400;700&display=swap">
<style>
  :root {
    --backdrop: #d3d4d6;
    --paper: #ffffff;
    --ink: #3a3a3b;
    --flap: #3b3b3c;
    --flap-text: #ffffff;
    --shadow: rgba(0,0,0,0.38);
  }
  * { margin: 0; padding: 0; box-sizing: border-box; }
  html, body { width: 993px; height: 1200px; overflow: hidden; }
  body { background: var(--backdrop); position: relative; font-family: "Roboto", Arial, sans-serif; color: var(--ink); }

  .sheet {
    position: absolute;
    background: var(--paper);
    box-shadow: 4px 6px 8px var(--shadow);
  }

  .brand {
    position: absolute;
    display: flex;
    flex-direction: column;
    align-items: center;
    text-align: center;
  }
  .brand__square {
    width: 24px; height: 24px;
    background: var(--ink);
    margin-bottom: 5px;
  }
  .brand__name {
    font-family: "Roboto", Arial, sans-serif;
    font-weight: 700;
    font-size: 9px;
    line-height: 9px;
    letter-spacing: 0.2px;
    color: var(--ink);
  }
  .brand__address {
    margin-top: 5px;
    font-size: 5.6px;
    line-height: 6.6px;
    font-weight: 400;
    color: var(--ink);
    white-space: nowrap;
  }
  .brand--small .brand__square { width: 18px; height: 18px; margin-bottom: 4px; }
  .brand--small .brand__name { font-size: 7.5px; line-height: 8px; }
  .brand--small .brand__address { font-size: 4.4px; line-height: 5.2px; margin-top: 3px; }

  .envelope-flap {
    position: absolute;
    left: 0; top: 0;
    width: 100%;
    height: 64px;
  }
  .envelope-flap path { fill: var(--flap); }
  .envelope-flap__tagline {
    position: absolute;
    left: 0; top: 27px;
    width: 100%;
    text-align: center;
    font-family: "Michroma", "Roboto", sans-serif;
    font-size: 8px;
    letter-spacing: 1px;
    color: var(--flap-text);
  }
</style>
</head>
<body>

  <!-- Letterhead -->
  <section class="sheet letterhead" style="left:118px; top:106px; width:363px; height:514px;">
    <div class="brand" style="left:8px; top:28px; width:160px;">
      <div class="brand__square"></div>
      <div class="brand__name">GREYMARSH<br>CONTRACTS</div>
      <div class="brand__address">Greymarsh Engineering Contracts LLP<br>Block No.317, Wing C, Tulvo Trade Court,<br>Manek Pural Road, Ruparel Industrial Estate,<br>Goregaon(E), Mumbai - 400 063</div>
    </div>
  </section>

  <section class="sheet envelope envelope--large" style="left:512px; top:106px; width:362px; height:515px;">
    <svg class="envelope-flap" viewBox="0 0 362 64" preserveAspectRatio="none" aria-hidden="true">
      <path d="M0 0 H362 L352 56 Q350 64 342 64 H20 Q12 64 10 56 Z"/>
    </svg>
    <div class="envelope-flap__tagline">ENGINEERED TO EXCELLENCE.</div>
  </section>

  <!-- Medium envelope -->
  <section class="sheet envelope-front" style="left:118px; top:644px; width:366px; height:260px;">
    <div class="brand" style="left:10px; top:33px; width:160px;">
      <div class="brand__square"></div>
      <div class="brand__name">GREYMARSH<br>CONTRACTS</div>
      <div class="brand__address">Greymarsh Engineering Contracts LLP<br>Block No.317, Wing C, Tulvo Trade Court,<br>Manek Pural Road, Ruparel Industrial Estate,<br>Goregaon(E), Mumbai - 400 063</div>
    </div>
  </section>

  <section class="sheet envelope" style="left:509px; top:644px; width:365px; height:260px;">
    <svg class="envelope-flap" viewBox="0 0 365 64" preserveAspectRatio="none" aria-hidden="true">
      <path d="M0 0 H365 L355 55 Q353 63 345 63 H20 Q12 63 10 55 Z"/>
    </svg>
    <div class="envelope-flap__tagline">ENGINEERED TO EXCELLENCE.</div>
  </section>

  <!-- Small envelope -->
  <section class="sheet envelope-front" style="left:118px; top:923px; width:365px; height:170px;">
    <div class="brand brand--small" style="left:6px; top:22px; width:116px;">
      <div class="brand__square"></div>
      <div class="brand__name">GREYMARSH<br>CONTRACTS</div>
      <div class="brand__address">Greymarsh Engineering Contracts LLP<br>Block No.317, Wing C, Tulvo Trade Court,<br>Manek Pural Road, Ruparel Industrial Estate,<br>Goregaon(E), Mumbai - 400 063</div>
    </div>
  </section>

  <section class="sheet envelope" style="left:510px; top:923px; width:364px; height:170px;">
    <svg class="envelope-flap" viewBox="0 0 364 63" preserveAspectRatio="none" aria-hidden="true">
      <path d="M0 0 H364 L354 55 Q352 63 344 63 H20 Q12 63 10 55 Z"/>
    </svg>
    <div class="envelope-flap__tagline">ENGINEERED TO EXCELLENCE.</div>
  </section>

</body>
</html>
```